Brookvane Consulting Business Card Design

Business Card Design for Brookvane Consulting. Brookvane Consulting is a boutique consultancy based in Atlanta, GA., that specializes in marketing strategy, organization planning, and leadership development. We provide solutions for small businesses and startups as well as Vantage 300 companies.

http://brookvaneconsulting.com/

Target Market(s)

We provide solutions for small businesses and startups as well as Vantage 300 companies.

Industry/Entity Type

Consulting

Contact Information for Business Card

Two sided business card with priority on contact information, logo, tag line (Inspiration to Dream More, Do More, Become More)

Colors

Designer to choose colors to be used in the design.

Requirements
Must have
• contact information, logo, tag line (Inspiration to Dream More, Do More, Become More)
• Simple no over communication.
Nice to have
• I would like to see different placements of logo and creative use of both sides of the card
Should not have
• Do not put too much information on the card.

```html
<!DOCTYPE html>
<html lang="en">
<head>
<meta charset="utf-8">
<title>Brookvane Consulting Business Card</title>
<link href="https://fonts.googleapis.com/css2?family=Lato:wght@400;700&family=Playball&display=swap" rel="stylesheet">
<style>
  :root {
    --backdrop: #9b9b9b;
    --card: #ffffff;
    --ink: #2b2b2b;
    --band: #3a3a3a;
    --band-text: #ffffff;
    --tip: #d9d9d9;
    --shadow: rgba(0, 0, 0, 0.35);
  }
  * { margin: 0; padding: 0; box-sizing: border-box; }
  html, body {
    width: 1200px;
    height: 900px;
    overflow: hidden;
    background: var(--backdrop);
  }
  .stage { position: relative; width: 1200px; height: 900px; }
  .card {
    position: absolute;
    top: 306px;
    width: 440px;
    height: 271px;
    background: var(--card);
    box-shadow: 2px 3px 4px var(--shadow);
    overflow: hidden;
    color: var(--ink);
  }
  .card--front { left: 149px; }
  .card--back { left: 609px; }

  .edge-band {
    position: absolute;
    top: 76px;
    bottom: 0;
    width: 50px;
    background: var(--band);
  }
  .card--front .edge-band { right: 0; }
  .card--back .edge-band { left: 0; }
  .edge-tip {
    position: absolute;
    top: 0;
    width: 50px;
    height: 76px;
    background: var(--tip);
  }
  .card--front .edge-tip { right: 0; }
  .card--back .edge-tip { left: 0; }
  .edge-url {
    position: absolute;
    top: 50%;
    left: 50%;
    transform: translate(-50%, -50%) rotate(90deg);
    white-space: nowrap;
    font-family: "Lato", sans-serif;
    font-size: 12px;
    letter-spacing: 0.2px;
    color: var(--band-text);
  }

  .brand {
    position: absolute;
    left: 24px;
    top: 54px;
    font-family: "Lato", sans-serif;
    font-weight: 700;
    font-size: 30px;
    line-height: 1.1;
    color: var(--ink);
  }
  .person {
    position: absolute;
    left: 24px;
    top: 160px;
    font-family: "Lato", sans-serif;
  }
  .person__name {
    font-size: 17px;
    font-weight: 700;
    text-transform: uppercase;
    letter-spacing: 0.2px;
  }
  .person__role { font-size: 13px; margin-top: 1px; }
  .contact {
    position: absolute;
    left: 24px;
    top: 213px;
    font-family: "Lato", sans-serif;
    font-size: 13px;
    line-height: 18px;
    list-style: none;
  }
  .contact li { display: flex; align-items: center; gap: 4px; }
  .contact svg { width: 10px; height: 10px; fill: var(--ink); }

  .tagline {
    position: absolute;
    left: 50px;
    right: 0;
    top: 92px;
    text-align: center;
    font-family: "Playball", cursive;
    font-size: 31px;
    line-height: 45px;
    color: var(--ink);
  }
</style>
</head>
<body>
<main class="stage">
  <section class="card card--front" aria-label="Card front">
    <p class="brand">Brookvane Consulting</p>
    <div class="person">
      <p class="person__name">Daniel Whitfield</p>
      <p class="person__role">Managing Director</p>
    </div>
    <ul class="contact">
      <li>
        <svg viewBox="0 0 10 10" aria-hidden="true"><path d="M2 1 L4 1 L4.6 3 L3.4 4 Q4.4 6 6 6.6 L7 5.4 L9 6 L9 8 Q9 9 8 9 Q1 8.4 1 2 Q1 1 2 1Z"/></svg>
        444 555 0192
      </li>
      <li>
        <svg viewBox="0 0 10 10" aria-hidden="true"><path d="M0.5 2 H9.5 V8 H0.5Z M0.5 2 L5 5.5 L9.5 2" /></svg>
        hello@brookvane.com
      </li>
    </ul>
    <div class="edge-tip" role="img" aria-label="Pencil tip illustration"></div>
    <div class="edge-band"><span class="edge-url">www.brookvaneconsulting.com</span></div>
  </section>

  <section class="card card--back" aria-label="Card back">
    <div class="edge-tip" role="img" aria-label="Pencil tip illustration"></div>
    <div class="edge-band"><span class="edge-url">www.brookvaneconsulting.com</span></div>
    <p class="tagline">Inspiration to<br>Dream More<br>Do More, Become More</p>
  </section>
</main>
</body>
</html>
```